Manuka Honey company needs a Upmarket, Luxury Website!

New Zealand, Taranaki based Manuka Honey company Rimu Vale Honey is looking for a new website, we are looking for an upmarket, luxury, serious website design. We export the highest quality quality Manuka Honey, straight from the Taranaki region.

Main export markets are Asia & Europe, also New Zealand & Australia.

Looking to have a beautiful, upmarket, serious, luxurious & graphical experience with mobile optimization in mind. Like the use of product staging/mockups

You can use copy from other websites to build the site and we will change the copy after the design is finished.

***Please include 'Honey Product' mockups in website.

*Will add illustrator files in coming days***

Feel free to make website functional in Shopify, Wordpress or WIX

Target Market(s)

Asia, Europe (main markets) New Zealand, Australia (Submarkets)

Coding

Coded - Design and coding required

Number of Pages Required

4 page

Requirements
Must have
• Home, Shop, About Us, Contact Us

Homepage to include:

Our Products
Company Video (video under construction)
What is MGO/KPS
Newsletter Opt-in

***(Not in Order)***

Please include 'Honey Product' mockups in website.
*Will add illustrator files in coming days
Nice to have
• FAQ & Partnership Inquiries (hyperlink in footer)

```html
<!DOCTYPE html>
<html lang="en">
<head>
<meta charset="utf-8">
<title>Rimu Vale Honey</title>
<link href="https://fonts.googleapis.com/css2?family=Nunito+Sans:wght@400;600;700;800&display=swap" rel="stylesheet">
<style>
:root{
  --ink:#1c1c1c;
  --ink-2:#232323;
  --gold:#a58b4f;
  --gold-band:#9a7f4a;
  --gold-light:#d6c08a;
  --gold-dark:#7d6432;
  --text:#e9e6df;
  --white:#ffffff;
}
*{box-sizing:border-box;margin:0;padding:0}
html,body{width:1200px;height:3658px;overflow:hidden;background:var(--ink);font-family:"Nunito Sans",sans-serif;color:var(--text)}
.page{position:relative;width:1200px;height:3658px;overflow:hidden;background:var(--ink)}
.abs{position:absolute}
.btn{position:absolute;display:flex;align-items:center;justify-content:center;gap:8px;border-radius:30px;
  background:linear-gradient(180deg,var(--gold-light),var(--gold) 55%,var(--gold-dark));
  color:var(--white);font-weight:700;font-size:16px;text-transform:uppercase;letter-spacing:.3px}
.btn .arrow{width:14px;height:14px;border-radius:50%;background:var(--white);position:relative}
.btn .arrow::after{content:"";position:absolute;left:4px;top:4px;width:4px;height:4px;border-top:2px solid var(--gold);border-right:2px solid var(--gold);transform:rotate(45deg)}
.heading{position:absolute;left:0;width:1200px;text-align:center;font-weight:800;text-transform:uppercase;color:var(--gold);font-size:50px;letter-spacing:.5px}
.copy{position:absolute;text-align:center;font-size:15.5px;line-height:26.5px;color:var(--text)}

/* header */
.site-header{position:absolute;top:0;left:0;width:1200px;height:95px;background:var(--ink)}
.brand{position:absolute;left:142px;top:30px;display:flex;align-items:center;gap:12px;color:var(--gold);font-size:25px;letter-spacing:3px;font-weight:600;text-transform:uppercase}
.brand .dot{width:34px;height:34px;border-radius:50%;border:2px solid var(--gold)}
.nav{position:absolute;top:38px;left:532px;display:flex;gap:0;font-size:12.5px;text-transform:uppercase;color:var(--white)}
.nav a{color:inherit;text-decoration:none;position:absolute;white-space:nowrap}
.nav a.active{color:var(--gold-light)}
.nav .marker{position:absolute;left:0;top:56px;width:38px;height:3px;background:var(--gold-light)}

/* hero */
.hero{position:absolute;top:95px;left:0;width:1200px;height:620px;
  background:radial-gradient(ellipse 420px 330px at 600px 300px,#2e4f9c 0%,#22397a 45%,rgba(80,45,25,.9) 80%),linear-gradient(90deg,#5a3019,#3a2a2a 50%,#4c2c1c)}
.hero-title{position:absolute;top:262px;left:0;width:1200px;text-align:center;font-size:86px;font-weight:700;color:var(--white);text-transform:uppercase;letter-spacing:-1px}
.hero-sub{position:absolute;top:382px;left:0;width:1200px;text-align:center;font-size:21px;font-weight:700;color:var(--white)}
.dots{position:absolute;top:555px;left:556px;display:flex;gap:9px}
.dots span{width:10px;height:10px;border-radius:50%;background:var(--white)}
.dots span.on{background:none;border:2px solid var(--white)}

/* video */
.mgo-band{position:absolute;top:1233px;left:0;width:1200px;height:636px;background:var(--gold-band)}
.video-frame{position:absolute;left:278px;top:1054px;width:644px;height:342px;background:var(--gold-band)}
.video{position:absolute;left:294px;top:1071px;width:611px;height:325px;background:linear-gradient(135deg,#4a4238,#2b2824 50%,#5d5244)}
.play{position:absolute;left:553px;top:1187px;width:94px;height:94px;border-radius:50%;border:6px solid var(--white)}
.play::after{content:"";position:absolute;left:34px;top:22px;border-left:30px solid var(--white);border-top:19px solid transparent;border-bottom:19px solid transparent}

/* products */
.product-ring{position:absolute;left:621px;top:1944px;width:434px;height:434px;border-radius:50%;background:linear-gradient(160deg,var(--gold-dark),var(--gold-light) 60%,var(--gold))}
.product-photo{position:absolute;left:632px;top:1955px;width:412px;height:412px;border-radius:50%;background:linear-gradient(180deg,#6f8fc4 0%,#a7b7c8 25%,#3f5a33 45%,#4d7a36 100%)}
.gallery-item{position:absolute;top:2461px;height:290px;width:287px}
.g1{left:0;background:linear-gradient(180deg,#c9d2dc,#4f6b3b 45%,#7d8c4a)}
.g2{left:304px;background:linear-gradient(180deg,#2f62c0,#8fa9d6 50%,#4b5d3e)}
.g3{left:609px;background:linear-gradient(180deg,#c7c9c4,#7d7460 45%,#8a8073)}
.g4{left:913px;background:linear-gradient(180deg,#3d72cf,#3f6a35 50%,#6e7c54)}
.g-arrow{position:absolute;top:2579px;width:34px;height:48px;background:var(--ink-2)}
.g-arrow::after{content:"";position:absolute;top:18px;width:11px;height:11px;border-top:2px solid var(--white);border-right:2px solid var(--white)}
.g-prev{left:0}.g-prev::after{left:13px;transform:rotate(-135deg)}
.g-next{right:0}.g-next::after{left:9px;transform:rotate(45deg)}

/* newsletter */
.signup{position:absolute;left:291px;top:3012px;width:614px;height:48px;border-radius:24px;background:var(--ink-2)}
.signup .field{position:absolute;left:30px;top:15px;font-size:12px;color:var(--white)}
.signup .btn{left:493px;top:3px;width:118px;height:42px;font-size:15px}

/* footer */
.footer-badge{position:absolute;left:176px;top:3296px;width:204px;height:204px;border-radius:50%;border:2px solid var(--gold);display:flex;align-items:center;justify-content:center;text-align:center;color:var(--gold);font-size:22px;font-weight:600;text-transform:uppercase;letter-spacing:2px;line-height:30px}
.foot-title{position:absolute;top:3318px;font-size:21px;font-weight:700;color:var(--white);text-transform:uppercase}
.foot-links{position:absolute;left:476px;top:3368px;list-style:none;font-size:15.5px;line-height:30.3px;color:var(--white)}
.social{position:absolute;top:3374px;width:48px;height:48px;border-radius:50%;border:2px solid var(--white)}
.rule{position:absolute;left:143px;top:3574px;width:914px;height:1px;background:#333}
.legal{position:absolute;top:3613px;left:0;width:1200px;text-align:center;font-size:12px;color:var(--white)}
</style>
</head>
<body>
<div class="page">

  <header class="site-header">
    <div class="brand"><span class="dot"></span>Rimu Vale Honey</div>
    <nav class="nav">
      <a class="active" style="left:0">Home</a>
      <a style="left:64px">Products</a>
      <a style="left:158px">About</a>
      <a style="left:229px">What is MGO</a>
      <a style="left:340px">FAQ &amp; Partnership Inquiries</a>
      <span class="marker"></span>
    </nav>
  </header>

  <section class="hero" role="img" aria-label="Coastal sea cave opening onto a beach at sunset">
  </section>
  <h1 class="hero-title">Rimu Vale Honey</h1>
  <p class="hero-sub">Lorem ipsum dolor sit ameconsectetur adipiscing elit</p>
  <a class="btn" style="left:504px;top:442px;width:192px;height:54px">Get Started <span class="arrow"></span></a>
  <div class="dots"><span></span><span></span><span class="on"></span><span></span><span></span></div>

  <svg class="abs" style="left:0;top:600px" width="1200" height="120" viewBox="0 0 1200 120">
    <defs>
      <linearGradient id="goldLine" x1="0" x2="1">
        <stop offset="0" stop-color="#d6c08a"/><stop offset=".5" stop-color="#8c7038"/><stop offset="1" stop-color="#d6c08a"/>
      </linearGradient>
    </defs>
    <path d="M0 108 Q420 90 600 15 Q780 90 1200 108 L1200 120 L0 120Z" fill="#1c1c1c"/>
    <path d="M0 106 Q420 88 600 13 Q780 88 1200 106" fill="none" stroke="url(#goldLine)" stroke-width="5"/>
    <circle cx="600" cy="70" r="14" fill="none" stroke="#a58b4f" stroke-width="2"/>
  </svg>

  <h2 class="heading" style="top:778px">Welcome to Rimu Vale Honey</h2>
  <p class="copy" style="left:180px;top:877px;width:840px">Sed ut perspiciatis unde omnis iste natus error sit voluptatem accusantium doloremque laudantiuotam rem aperiam, eaque ipsa quae ab illo inventore veritatis et quasi architecto beatae vitae dicta sunt explicaboemo enim ipsam voluptatem quia voluptas sit aspernatur aut odit aut fused quia consequuntur magni dolores eosrationoluptatem sequi nesciuneque porro quisquam est, qui dolorem ipsum quia dolor sit ametconsectetur</p>

  <div class="mgo-band"></div>
  <div class="video-frame"></div>
  <div class="video" role="img" aria-label="Company video still: beehive frames being inspected"></div>
  <div class="play"></div>

  <h2 class="heading" style="top:1492px;color:var(--white)">What is MGO</h2>
  <p class="copy" style="left:180px;top:1590px;width:840px">Sed ut perspiciatis unde omnis iste natus error sit voluptatem accusantium doloremque laudantiuotam rem aperiam, eaque ipsa quae ab illo inventore veritatis et quasi architecto beatae vitae dicta sunt explicaboemo enim ipsam voluptatem quia voluptas sit aspernatur aut odit aut fused quia consequuntur magni dolores eosrationoluptatem sequi nesciuneque porro quisquam est, qui dolorem ipsum quia dolor sit ametconsectetur</p>
  <a class="btn" style="left:504px;top:1735px;width:192px;height:54px">Read More <span class="arrow"></span></a>

  <h2 class="heading" style="left:143px;width:auto;top:1971px">Our Products</h2>
  <p class="copy" style="left:143px;top:2064px;width:445px;text-align:left">Sed ut perspiciatis unde omnis iste natus error sit voluptatem accusantium doloremque laudantiuotam rem aperiam, eaque ipsa quae ab illo inventore veritatis et quasi architecto beatae vitae dicta sunt explicaboemo enim ipsamvoluptatem voluptas sit aspernatur aut odit aut fused quia consequuntni dolores eosrationoluptatem sequi nesciuneque porro quisquam est, qui dolorem ipsum quiaametconsectetur</p>
  <a class="btn" style="left:143px;top:2286px;width:192px;height:53px">Read More <span class="arrow"></span></a>
  <div class="product-ring"></div>
  <div class="product-photo" role="img" aria-label="Beekeepers in suits beside hives in a green valley"></div>

  <div class="gallery-item g1" role="img" aria-label="River and bush-covered hills"></div>
  <div class="gallery-item g2" role="img" aria-label="Utility vehicles parked under a blue sky"></div>
  <div class="gallery-item g3" role="img" aria-label="Beekeeping team walking near hives"></div>
  <div class="gallery-item g4" role="img" aria-label="Hives on a grassy hillside"></div>
  <div class="g-arrow g-prev"></div>
  <div class="g-arrow g-next"></div>

  <h2 class="heading" style="top:2856px">Newsletter Sign Up</h2>
  <p class="copy" style="left:0;top:2934px;width:1200px">Sed ut perspiciatis unde omnis iste natus error sit voluptatem</p>
  <div class="signup">
    <span class="field">Enter Email</span>
    <a class="btn">Sign Up <span class="arrow"></span></a>
  </div>

  <svg class="abs" style="left:0;top:3130px" width="1200" height="120" viewBox="0 0 1200 120">
    <path d="M0 14 Q420 10 600 110 Q780 10 1200 14" fill="none" stroke="url(#goldLine)" stroke-width="9"/>
  </svg>

  <div class="footer-badge">Rimu Vale<br>Honey</div>

  <h3 class="foot-title" style="left:476px">Quick Links</h3>
  <ul class="foot-links">
    <li>Home</li><li>Products</li><li>About</li><li>What is MGO</li>
  </ul>

  <h3 class="foot-title" style="left:718px">Stay Connected</h3>
  <span class="social" style="left:719px"></span>
  <span class="social" style="left:774px"></span>
  <span class="social" style="left:829px"></span>
  <span class="social" style="left:886px"></span>
  <a class="btn" style="left:718px;top:3456px;width:304px;height:52px;font-size:16.5px">FAQ &amp; Partnership Inquiries</a>

  <div class="rule"></div>
  <p class="legal">© 2021 Rimu Vale Honey.All Rights Reserved &nbsp;|&nbsp; Privacy Policy &nbsp;|&nbsp; Terms and use</p>

</div>
</body>
</html>
```